Coastal Learner Bureau business cards

Australian company about to start offering its services. We recruit international students to come to study English, vocational education and postgraduate courses in Australia. We help them find the institution and select the right city they want to come to Australia. We are a young, online oriented and supportive agency. Our clients are between 18 and 35 years old, mainly University students, young professionals or people with work experience. We provide much more information that any other agency offer. We administrate a Facebook group with more than 11.000 members that daily ask questions about general information when coming to Australia, while they are here and even after they leave the country

Target Market(s)

International students from South America, Central America and Europe

Industry/Entity Type

Student

Contact Information for Business Card

Tomas Bilbrea
Managing Director
tomas@kelvarin.com.au
www.kelvoria.com.au
+61 491058264
Melbourne, Australia

Font styles to use
Serif
Sans Serif

Colors

Designer to choose colors to be used in the design.

Requirements
Must have
• Horizontal design
• Standard business card size and shape. If font uses green or yellow colours, they will have to match the ones from the logo
Nice to have
• UPDATE: Use the contents of the green image to design one of the card sides. Use our logo in the background of that side as watermark.
• Passport image, or immigration stamps. A picture of the Yarra River (from Melbourne) would be cool as well.
Should not have
• Non-standard business card size and shape
• Not black as the background colour of any sides as we are not a VIP agency or a hight class service. We are orientes to young people and they like colours, pictures, something attractive.
• Vertical design
• NO YELLOW or BLACK AS THE BACKGROUND COLOUR OF ANY SIDE OF THE BIZ CARD

```html
<!DOCTYPE html>
<html lang="en">
<head>
<meta charset="utf-8">
<title>Coastal Learner Bureau business cards</title>
<link rel="stylesheet" href="https://fonts.googleapis.com/css2?family=Jost:wght@400;500;600;700&display=swap">
<style>
  :root {
    --backdrop: #8e8d8e;
    --brand-green: #135f43;
    --card-white: #ffffff;
    --text-grey: #4a4a4a;
    --shadow: rgba(0,0,0,0.28);
  }
  * { margin: 0; padding: 0; box-sizing: border-box; }
  html, body { width: 1200px; height: 929px; overflow: hidden; }
  body {
    background: var(--backdrop);
    font-family: "Jost", sans-serif;
    position: relative;
  }
  .card {
    position: absolute;
    width: 520px;
    height: 297px;
    box-shadow: 0 6px 14px var(--shadow);
    overflow: hidden;
  }
  /* Front side */
  .card-front {
    left: 90px; top: 110px;
    background: var(--brand-green);
    color: var(--card-white);
  }
  .front-brand {
    position: absolute;
    left: 0; right: 0; top: 100px;
    text-align: center;
    font-size: 54px;
    font-weight: 500;
    letter-spacing: 1px;
    color: var(--card-white);
  }
  .front-tagline {
    position: absolute;
    left: 0; right: 0; bottom: 30px;
    text-align: center;
    font-size: 13px;
    font-weight: 500;
    letter-spacing: 1.2px;
  }
  /* Back side */
  .card-back {
    left: 590px; top: 480px;
    background: var(--card-white);
  }
  .back-brand {
    position: absolute;
    left: 36px; top: 48px;
    font-size: 40px;
    font-weight: 500;
    color: var(--brand-green);
    letter-spacing: 0.5px;
  }
  .edge-tab {
    position: absolute;
    right: -8px; top: 46px;
    width: 20px; height: 38px;
    border-radius: 8px;
    background: var(--brand-green);
  }
  .holder {
    position: absolute;
    right: 56px; top: 100px;
    text-align: right;
  }
  .holder-name {
    font-size: 23px;
    font-weight: 700;
    color: var(--brand-green);
    letter-spacing: 0.6px;
    line-height: 1;
  }
  .holder-role {
    font-size: 14px;
    color: var(--text-grey);
    letter-spacing: 0.6px;
    margin-top: 4px;
  }
  .divider {
    position: absolute;
    left: 36px; top: 160px;
    width: 270px; height: 2px;
    background: var(--brand-green);
  }
  .location {
    position: absolute;
    right: 36px; top: 190px;
    text-align: right;
    font-size: 13px;
    line-height: 1.35;
    color: var(--text-grey);
    letter-spacing: 0.8px;
  }
  .contact-list {
    position: absolute;
    left: 36px; top: 176px;
    list-style: none;
  }
  .contact-item {
    display: flex;
    align-items: center;
    gap: 12px;
    font-size: 14px;
    color: var(--text-grey);
    letter-spacing: 0.8px;
    height: 23px;
  }
  .contact-item svg { width: 12px; height: 12px; flex: none; }
</style>
</head>
<body>
  <section class="card card-front" aria-label="Front of business card">
    <div class="front-brand">Kelvoria</div>
    <p class="front-tagline">Hacemos más por ti!</p>
  </section>

  <section class="card card-back" aria-label="Back of business card">
    <div class="back-brand">Kelvoria</div>
    <div class="edge-tab"></div>
    <div class="holder">
      <div class="holder-name">TOMAS BILBREA</div>
      <div class="holder-role">Managing Director</div>
    </div>
    <div class="divider"></div>
    <ul class="contact-list">
      <li class="contact-item">
        <svg viewBox="0 0 12 12" aria-hidden="true"><rect x="2.5" y="0.8" width="7" height="10.4" rx="1.2" fill="none" stroke="#135f43" stroke-width="1.3"/><line x1="5" y1="9.3" x2="7" y2="9.3" stroke="#135f43" stroke-width="1"/></svg>
        +61 491058264
      </li>
      <li class="contact-item">
        <svg viewBox="0 0 12 12" aria-hidden="true"><rect x="0.5" y="2" width="11" height="8" rx="1" fill="#135f43"/><polyline points="1,2.6 6,6.5 11,2.6" fill="none" stroke="#fff" stroke-width="1"/></svg>
        tomas@kelvarin.com.au
      </li>
      <li class="contact-item">
        <svg viewBox="0 0 12 12" aria-hidden="true"><circle cx="5" cy="5" r="3.4" fill="none" stroke="#135f43" stroke-width="1.6"/><line x1="7.5" y1="7.5" x2="11" y2="11" stroke="#135f43" stroke-width="2" stroke-linecap="round"/></svg>
        www.kelvoria.com.au
      </li>
    </ul>
    <p class="location">Melbourne,<br>Australia</p>
  </section>
</body>
</html>
```